Concierge Healthcare Business Card Design and Logo

We need a logo and business card design for a new company called "Sound Haven". We will provide concierge audiological care, hearing aids, hearing exams, custom hearing protection etc to patients in the comfort of their homes and offices. We would like a sleek and modern design preferably with an Ear related logo.

Target Market(s)

People with hearing loss, Hunters, Musicians
My usual clientele are older individuals so usually 50+ years old

Industry/Entity Type

Health Care

Contact Information for Business Card

Celia Brandt, AuD
Audiologist
512-648-2917
soundhaven@mailvoro.com
www.soundhaven-vorel.com

Logo Text

Sound Haven

Number of Pages Required

3 page

```html
<!DOCTYPE html>
<html lang="en">
<head>
<meta charset="utf-8">
<title>Sound Haven – Business Card</title>
<link rel="stylesheet" href="https://fonts.googleapis.com/css2?family=Montserrat:wght@400;500;600&display=swap">
<style>
  :root {
    --backdrop: #2a2a2c;
    --card-white: #ffffff;
    --ink: #0b0b0b;
    --brand-blue: #1ea7e4;
    --text-light: #ffffff;
  }
  * { box-sizing: border-box; margin: 0; padding: 0; }
  html, body {
    width: 1200px;
    height: 900px;
    overflow: hidden;
    background: var(--backdrop);
    font-family: "Montserrat", sans-serif;
  }
  .canvas {
    position: relative;
    width: 1200px;
    height: 900px;
  }
  .card {
    position: absolute;
    left: 267px;
    width: 666px;
    height: 380px;
    background: var(--card-white);
    border-radius: 20px;
    overflow: hidden;
  }
  .card--front { top: 50px; }
  .card--back { top: 470px; }

  /* Front */
  .front-mark {
    position: absolute;
    left: 50%;
    top: 62px;
    width: 124px;
    height: 124px;
    margin-left: -62px;
    border-radius: 50%;
    border: 5px solid var(--brand-blue);
  }
  .front-name {
    position: absolute;
    top: 208px;
    width: 100%;
    text-align: center;
    font-size: 30px;
    font-weight: 600;
    letter-spacing: 3px;
    color: var(--ink);
  }
  .front-url {
    position: absolute;
    top: 276px;
    width: 100%;
    text-align: center;
    font-size: 17px;
    font-weight: 500;
    color: var(--ink);
  }
  .front-url .url-domain { color: var(--brand-blue); }

  /* Back */
  .back-art {
    position: absolute;
    inset: 0;
  }
  .back-brand {
    position: absolute;
    left: 36px;
    top: 170px;
    display: flex;
    align-items: center;
    gap: 14px;
  }
  .back-brand__mark {
    width: 58px;
    height: 58px;
    border-radius: 50%;
    border: 4px solid var(--brand-blue);
  }
  .back-brand__rule {
    width: 2px;
    height: 54px;
    background: var(--ink);
  }
  .back-brand__name {
    font-size: 23px;
    font-weight: 600;
    letter-spacing: 2.5px;
    color: var(--ink);
  }
  .contact {
    position: absolute;
    right: 22px;
    top: 192px;
    text-align: right;
    color: var(--text-light);
  }
  .contact__name {
    font-size: 19px;
    font-weight: 600;
    color: var(--brand-blue);
    margin-right: 26px;
  }
  .contact__title {
    font-size: 14px;
    font-weight: 400;
    margin: 2px 26px 6px 0;
  }
  .contact__row {
    display: flex;
    justify-content: flex-end;
    align-items: center;
    gap: 10px;
    font-size: 14px;
    font-weight: 400;
    line-height: 23px;
  }
  .contact__row svg { width: 16px; height: 16px; flex: none; }
</style>
</head>
<body>
<main class="canvas">

  <section class="card card--front" aria-label="Card front">
    <div class="front-mark"></div>
    <p class="front-name">Sound Haven</p>
    <p class="front-url">www.<span class="url-domain">soundhaven-vorel</span>.com</p>
  </section>

  <section class="card card--back" aria-label="Card back">
    <svg class="back-art" viewBox="0 0 666 380" width="666" height="380" aria-hidden="true">
      <path transform="translate(-18 -10)" d="M540 0 C560 100 470 160 420 210 C370 260 300 340 60 380 L0 380 L0 400 L700 400 L700 0 Z" fill="var(--brand-blue)"/>
      <path transform="translate(-9 -5)" d="M540 0 C560 100 470 160 420 210 C370 260 300 340 60 380 L0 380 L0 400 L700 400 L700 0 Z" fill="var(--card-white)"/>
      <path d="M540 0 C560 100 470 160 420 210 C370 260 300 340 60 380 L700 380 L700 0 Z" fill="var(--ink)"/>
      <path d="M0 362 C120 366 220 360 300 346" fill="none" stroke="var(--ink)" stroke-width="7"/>
      <path d="M0 376 C100 378 180 376 250 372" fill="none" stroke="var(--brand-blue)" stroke-width="8"/>
      <path d="M560 40 L666 40 L666 56 L590 56 Z" fill="var(--brand-blue)"/>
      <circle cx="578" cy="96" r="60" fill="var(--card-white)" stroke="var(--ink)" stroke-width="4"/>
      <circle cx="578" cy="96" r="50" fill="none" stroke="var(--brand-blue)" stroke-width="5"/>
    </svg>

    <div class="back-brand">
      <div class="back-brand__mark"></div>
      <div class="back-brand__rule"></div>
      <span class="back-brand__name">Sound Haven</span>
    </div>

    <div class="contact">
      <p class="contact__name">Celia Brandt, AuD</p>
      <p class="contact__title">Audiologist</p>
      <p class="contact__row">512-648-2917
        <svg viewBox="0 0 16 16" aria-hidden="true"><path d="M4 1.5 L6.5 4.5 L5 6.3 C6 8.3 7.7 10 9.7 11 L11.5 9.5 L14.5 12 L13 14.3 C7.5 14 2 8.5 1.7 3 Z" fill="var(--brand-blue)"/></svg>
      </p>
      <p class="contact__row">soundhaven@mailvoro.com
        <svg viewBox="0 0 16 16" aria-hidden="true"><rect x="1.5" y="3.5" width="13" height="9" fill="none" stroke="var(--brand-blue)" stroke-width="1.5"/><path d="M1.5 3.5 L8 9 L14.5 3.5" fill="none" stroke="var(--brand-blue)" stroke-width="1.5"/></svg>
      </p>
      <p class="contact__row">www.soundhaven-vorel.com
        <svg viewBox="0 0 16 16" aria-hidden="true"><circle cx="8" cy="8" r="6.5" fill="none" stroke="var(--brand-blue)" stroke-width="1.5"/><ellipse cx="8" cy="8" rx="2.8" ry="6.5" fill="none" stroke="var(--brand-blue)" stroke-width="1.2"/><path d="M1.5 8 H14.5" stroke="var(--brand-blue)" stroke-width="1.2"/></svg>
      </p>
    </div>
  </section>

</main>
</body>
</html>
```